Letterhead, stationery and email signature for construction business

I need the letterhead, stationery and email signature designs for a construction business. I want them to have a corporate feel to them.

I've attached the logo for reference.

```html
<!DOCTYPE html>
<html lang="en">
<head>
<meta charset="utf-8">
<title>Halvern Projects — Business Card</title>
<link href="https://fonts.googleapis.com/css2?family=Raleway:wght@700;800&family=Roboto:wght@400;500&display=swap" rel="stylesheet">
<style>
  :root {
    --backdrop: #cfd3d4;
    --paper: #f4f4f3;
    --brand-blue: #1f3a9e;
    --deep-blue: #22338f;
    --ink: #2a2a2e;
    --muted: #4a4a50;
    --rule: #3a3a3e;
  }
  * { margin: 0; padding: 0; box-sizing: border-box; }
  html, body { width: 1200px; height: 1049px; overflow: hidden; }
  body {
    background: var(--backdrop);
    font-family: "Roboto", Arial, sans-serif;
    position: relative;
  }
  .card {
    position: absolute;
    left: 290px;
    width: 620px;
    height: 354px;
    box-shadow: 0 10px 28px rgba(0,0,0,0.18);
  }
  .card--front { top: 150px; background: var(--paper); }
  .card--back { top: 548px; background: var(--brand-blue); }

  .brand {
    position: absolute;
    right: 44px;
    top: 62px;
    text-align: right;
    font-family: "Raleway", Arial, sans-serif;
    font-weight: 800;
    color: var(--deep-blue);
    line-height: 1;
  }
  .brand__name { font-size: 40px; letter-spacing: 0.5px; }
  .brand__sub { font-size: 16px; letter-spacing: 9px; margin-top: 4px; margin-right: -9px; }

  .person {
    position: absolute;
    left: 40px;
    top: 150px;
  }
  .person__name {
    font-family: "Raleway", Arial, sans-serif;
    font-weight: 800;
    font-size: 19px;
    letter-spacing: 0.6px;
    color: var(--deep-blue);
    text-transform: uppercase;
  }
  .person__title {
    font-size: 15px;
    color: var(--ink);
    margin-top: 2px;
  }
  .rule {
    position: absolute;
    left: 160px;
    right: 44px;
    top: 194px;
    height: 1px;
    background: var(--rule);
  }
  .contacts {
    position: absolute;
    left: 40px;
    top: 212px;
    list-style: none;
  }
  .contacts li {
    display: flex;
    align-items: center;
    gap: 8px;
    font-size: 14px;
    color: var(--muted);
    line-height: 22px;
  }
  .contacts svg { width: 13px; height: 13px; flex: none; }
  .address {
    position: absolute;
    right: 44px;
    bottom: 34px;
    text-align: right;
    font-size: 15px;
    line-height: 21px;
    color: var(--muted);
  }

  .back-pattern {
    position: absolute;
    inset: 0;
    background: linear-gradient(135deg, #2444b0 0%, #1d3596 100%);
  }
  .back-name {
    position: absolute;
    left: 0; right: 0;
    top: 50%;
    transform: translateY(-50%);
    text-align: center;
    font-family: "Raleway", Arial, sans-serif;
    font-weight: 800;
    font-size: 30px;
    color: #eef0f5;
    letter-spacing: 1px;
  }
</style>
</head>
<body>

  <section class="card card--front">
    <div class="brand">
      <div class="brand__name">HALVERN</div>
      <div class="brand__sub">PROJECTS</div>
    </div>

    <div class="person">
      <div class="person__name">Daniel R. Whitcombe</div>
      <div class="person__title">Founder &amp; CEO</div>
    </div>

    <div class="rule"></div>

    <ul class="contacts">
      <li>
        <svg viewBox="0 0 16 16" aria-hidden="true"><path fill="#1f3a9e" d="M3.5 1 6 3.5 4.6 5.4c.9 2 2.5 3.6 4.5 4.5L11 8.5 13.5 11 12 14C6.5 13.6 2.4 9.5 2 4z"/></svg>
        (555)318-0472
      </li>
      <li>
        <svg viewBox="0 0 16 16" aria-hidden="true"><rect x="1.5" y="3.5" width="13" height="9" fill="none" stroke="#1f3a9e" stroke-width="1.4"/><path d="M1.5 3.5 8 9l6.5-5.5" fill="none" stroke="#1f3a9e" stroke-width="1.4"/></svg>
        info@halvernprojects.com
      </li>
      <li>
        <svg viewBox="0 0 16 16" aria-hidden="true"><circle cx="8" cy="8" r="6.3" fill="none" stroke="#1f3a9e" stroke-width="1.3"/><ellipse cx="8" cy="8" rx="2.8" ry="6.3" fill="none" stroke="#1f3a9e" stroke-width="1.1"/><path d="M1.7 8h12.6M2.8 5h10.4M2.8 11h10.4" stroke="#1f3a9e" stroke-width="1.1"/></svg>
        www.halvernprojects.com
      </li>
    </ul>

    <address class="address" style="font-style:normal">
      Halvern Project, Ltd.<br>
      2240 Cedar Ridge Avenue<br>
      Lakemont, CA 90000
    </address>
  </section>

  <section class="card card--back">
    <div class="back-pattern" role="img" aria-label="Embossed repeating brand symbol pattern on blue stock"></div>
    <div class="back-name">HALVERN</div>
  </section>

</body>
</html>
```